Site Redesign in WORDPRESS for a Aerial Survey Company

We are looking for an updated look to our website that reflects our aerial drone services. Our company is changing directions from helping to provide legal documentation for companies to operate UAVs for commercial operations, to now providing Aerial Data Collection services. We need the new website to focus on this new direction.

Wordpress Design (Uncoded - PSD layout only)

Current site: http://tornwickaviation.com/
Business card attached

VISUAL
********
The new pages should be visually top-notch, appealing, and more user-friendly to navigate, and represent our professionalism and level of expertise. We love the use of images, both great photography and technical. Our specialty is the use of Aerial LiDAR.

Our current site uses the Mallow template.

Colors: I've attached the Pantone for our logo colors

Fonts: Simple, clean and professional. We are not worried about specific fonts so long as they tie or compliment our logo.

STRUCTURE
****************
In the attached document I have laid out the pages we would like to have and the content outline of the content these pages will include.

We're happy to answer you questions in the comments and to provide quick feedback and additional info if necessary.

Target Market(s)

Agricultural and Engineering firms

Industry/Entity Type

Agribusiness

Coding

Coded - Design and coding required

Number of Pages Required

5+ page

Font styles to use
Sans Serif

Colors
0392cd
9bcb3c
ffffff

Requirements
Must have
• We need at a minimum a design with the Home/Landing, Services, and about. Need to be able to adapt the site as we add new services and increase our partnerships.
• Please provide in WordPress format.
• Links to social media: Facebook, Twitter, Instagram
Nice to have
• We like parrallax, but in the end it's about the overall feel of the site.
Should not have
• Please, professional designs only.

```html
<!DOCTYPE html>
<html lang="en">
<head>
<meta charset="utf-8">
<title>Tornwick Aviation</title>
<link href="https://fonts.googleapis.com/css2?family=Roboto:wght@300;400;500&display=swap" rel="stylesheet">
<style>
:root{
  --blue:#5b82c8;
  --blue-head:#6289cc;
  --green:#67ac3c;
  --green-dark:#4f9a2b;
  --text:#8a8a8a;
  --dark:#333;
  --band:#f6f5f5;
  --line:#e6e6e6;
  --footer:#1b1b1b;
  --contact:#5c80c7;
  --white:#fff;
}
*{margin:0;padding:0;box-sizing:border-box}
html,body{width:1200px;height:3689px;overflow:hidden}
body{position:relative;background:var(--white);font-family:"Roboto",Arial,sans-serif;color:var(--text);font-weight:300}
.abs{position:absolute}
a{color:inherit;text-decoration:none}

/* header */
.site-header{left:0;top:0;width:1200px;height:120px;background:var(--white)}
.brand{left:75px;top:26px;display:flex;align-items:center;gap:14px}
.brand-mark{width:50px;height:50px;background:var(--blue)}
.brand-name{font-size:30px;font-weight:500;color:var(--blue);letter-spacing:1px;line-height:1}
.search{left:932px;top:20px;width:194px;height:36px;border:1px solid var(--line);font-size:12px;padding:10px 12px;color:#aaa}
.search svg{position:absolute;right:10px;top:11px}
.main-nav{left:640px;top:68px;display:flex;font-size:13px;font-weight:400;color:#555}
.main-nav a{display:block;height:32px;line-height:32px;padding:0 20px;margin-right:12px}
.main-nav a.active{background:var(--blue);color:var(--white);padding:0 18px;margin-right:22px}

/* hero */
.hero{left:0;top:120px;width:1200px;height:618px;background:linear-gradient(180deg,#6d7e8e 0%,#8f97a0 45%,#c99b72 80%,#d98b4a 100%)}
.hero-dots{left:1127px;top:337px;display:flex;flex-direction:column;gap:7px}
.hero-dots span{width:12px;height:12px;border-radius:50%;border:2px solid var(--white)}
.hero-dots span.on{background:var(--white)}

/* section heads */
.section-title{width:1200px;left:0;text-align:center;font-weight:300;color:var(--blue-head);font-size:35px}
.section-sub{width:1200px;left:0;text-align:center;font-size:14px;color:#666;letter-spacing:.3px}

/* agriculture */
.band{left:0;width:1200px;background:var(--band)}
.service{width:340px;display:flex;gap:18px}
.service-icon{flex:none;width:82px;height:82px;border-radius:50%;background:var(--green);display:flex;align-items:center;justify-content:center}
.service h3{font-size:19px;font-weight:400;color:var(--dark);margin:2px 0 12px}
.service p{font-size:13px;line-height:19px;text-align:justify}
.read{display:block;margin-top:8px;font-size:12px;color:var(--green);font-weight:400}
.service.wide{width:510px}
.rule{left:75px;width:1050px;height:1px;background:var(--line)}

/* feature rows */
.photo{border-radius:50%}
.feature h2{font-size:27px;font-weight:300;color:var(--blue-head);line-height:32px;letter-spacing:.3px}
.feature p{font-size:14px;line-height:22px;text-align:justify;margin-top:22px}
.feature .more{display:block;margin-top:22px;font-size:14px;color:var(--blue-head);font-weight:400}

/* about */
.about-head{left:0;width:1200px;top:2905px;display:flex;justify-content:center;align-items:center;gap:36px}
.about-head h2{font-size:35px;font-weight:300;color:var(--green)}
.card{top:2975px;width:502px;height:175px;background:var(--white);border:1px solid var(--line);display:flex;gap:20px;padding:22px 24px}
.avatar{flex:none;width:132px;height:132px;border-radius:50%;border:4px solid var(--blue);background:linear-gradient(160deg,#c9c2b8,#8d8a86)}
.card h3{font-size:15px;font-weight:400;color:var(--green);margin:6px 0 12px}
.card p{font-size:13px;line-height:19px}
.card .read{margin-top:10px;font-size:13px}

/* contact */
.contact{left:0;top:3213px;width:1200px;height:359px;background:var(--contact)}
.contact-map{left:60px;top:3230px;width:1080px;height:330px;background:radial-gradient(ellipse at center,rgba(255,255,255,.14),rgba(255,255,255,0) 70%)}
.contact-title{left:0;top:3270px;width:1200px;text-align:center;color:var(--white);font-size:33px;font-weight:300;line-height:40px;letter-spacing:.5px}
.contact-box{left:385px;top:3338px;width:422px;height:118px;background:var(--white);padding:18px 24px;font-size:13px;line-height:19px}
.contact-box:before{content:"";position:absolute;left:197px;top:-14px;border:14px solid transparent;border-top:0;border-bottom-color:var(--white)}
.contact-box .name{color:var(--blue-head);font-weight:400}
.contact-lines{display:flex;gap:40px;margin-top:16px;color:var(--blue-head)}
.contact-lines span{display:flex;align-items:center;gap:8px}

/* footer */
.site-footer{left:0;top:3572px;width:1200px;height:117px;background:var(--footer)}
.footer-nav{left:75px;top:3610px;font-size:13px;color:#ddd;font-weight:400;letter-spacing:.5px}
.footer-nav span{margin:0 10px;color:#888}
.copyright{left:75px;top:3636px;font-size:12px;color:#bbb}
.social{left:905px;top:3610px;display:flex;gap:14px}
.social span{width:38px;height:38px;border-radius:50%;background:var(--white)}
</style>
</head>
<body>

<header class="site-header abs">
  <div class="brand abs">
    <div class="brand-mark"></div>
    <div class="brand-name">TORNWICK AVIATION</div>
  </div>
  <div class="search abs">Search
    <svg width="14" height="14" viewBox="0 0 14 14"><circle cx="6" cy="6" r="4.5" fill="none" stroke="#555" stroke-width="2"/><path d="M9.5 9.5L13 13" stroke="#555" stroke-width="2"/></svg>
  </div>
  <nav class="main-nav abs">
    <a class="active">HOME</a><a>ABOUT US</a><a>SERVICES</a><a>BLOG</a><a>CONTACT US</a>
  </nav>
</header>

<div class="hero abs" role="img" aria-label="Hands launching a quadcopter drone against a sunset sky"></div>
<div class="hero-dots abs"><span class="on"></span><span></span><span></span><span></span><span></span><span></span></div>

<h1 class="section-title abs" style="top:788px">OUR SERVICES</h1>
<p class="section-sub abs" style="top:838px">OUR TEAM OF AVIATION EXPERTS DEVELOP SOLUTIONS TO PREPARE YOUR BUSINESS TO BE A LEADER OF TOMORROW.</p>

<section class="band abs" style="top:895px;height:430px"></section>
<h2 class="section-title abs" style="top:938px;color:var(--green);font-size:33px">PRECISION AGRICULTURE</h2>

<div class="service abs" style="left:75px;top:1002px">
  <div class="service-icon"><svg width="34" height="34" viewBox="0 0 34 34"><path d="M6 28C6 14 14 6 28 6c0 14-8 22-22 22z" fill="#fff"/><path d="M8 26L22 12" stroke="#67ac3c" stroke-width="2"/></svg></div>
  <div><h3>Crop Management</h3><p>Sed ut perspiciatis unde omnis iste natus error sit voluptatem accusantium doloremque laudantium.</p><a class="read">READ MORE</a></div>
</div>
<div class="service abs" style="left:435px;top:1002px">
  <div class="service-icon"><svg width="30" height="36" viewBox="0 0 30 36"><path d="M15 2a12 12 0 0 1 12 12c0 9-12 20-12 20S3 23 3 14A12 12 0 0 1 15 2z" fill="#fff"/><circle cx="15" cy="14" r="4.5" fill="#67ac3c"/></svg></div>
  <div><h3>Land Surveying</h3><p>Sed ut perspiciatis unde omnis iste natus error sit voluptatem accusantium doloremque laudantium.</p><a class="read">READ MORE</a></div>
</div>
<div class="service abs" style="left:795px;top:1002px">
  <div class="service-icon"><svg width="32" height="32" viewBox="0 0 32 32"><path d="M6 4v26" stroke="#fff" stroke-width="2.5"/><path d="M7 5h20l-4 6 4 6H7" fill="none" stroke="#fff" stroke-width="2.5" stroke-linejoin="round"/></svg></div>
  <div><h3>Yield Forecasting</h3><p>Sed ut perspiciatis unde omnis iste natus error sit voluptatem accusantium doloremque laudantium.</p><a class="read">READ MORE</a></div>
</div>

<div class="rule abs" style="top:1138px"></div>

<div class="service wide abs" style="left:75px;top:1162px">
  <div class="service-icon"><svg width="34" height="34" viewBox="0 0 34 34"><path d="M17 31V12" stroke="#fff" stroke-width="2.5"/><path d="M17 20c-6 0-10-4-10-9 6 0 10 4 10 9zM17 16c0-6 4-10 10-10 0 6-4 10-10 10z" fill="#fff"/></svg></div>
  <div><h3>NDVI, SAVI, and other Vegetation Indices</h3><p>Sed ut perspiciatis unde omnis iste natus error sit voluptatem accusantium doloremque laudantium. Sed ut perspiciatis unde omnis iste natus error sit voluptatem accusantium.</p><a class="read">READ MORE</a></div>
</div>
<div class="service wide abs" style="left:622px;top:1162px">
  <div class="service-icon"><svg width="38" height="26" viewBox="0 0 38 26"><path d="M2 13C8 4 30 4 36 13 30 22 8 22 2 13z" fill="#fff"/><circle cx="19" cy="13" r="6" fill="#67ac3c"/><circle cx="19" cy="13" r="2.5" fill="#fff"/></svg></div>
  <div><h3>Insurance Monitoring</h3><p>Sed ut perspiciatis unde omnis iste natus error sit voluptatem accusantium doloremque laudantium. Sed ut perspiciatis unde omnis iste natus error sit voluptatem accusantium.</p><a class="read">READ MORE</a></div>
</div>

<div class="photo abs" style="left:152px;top:1362px;width:286px;height:286px;background:linear-gradient(180deg,#c9c6bd,#8b9296 55%,#2d4760)" role="img" aria-label="Offshore oil platform at sea"></div>
<div class="feature abs" style="left:477px;top:1398px;width:648px">
  <h2>EXPLORATION, OIL, GAS, &amp; MINERAL</h2>
  <p>Sed ut perspiciatis unde omnis iste natus error sit voluptatem accusantium doloremque laudantium, totam rem aperiam, eaque ipsa quae ab illo inventore veritatis et quasi architecto beatae vitae dicta sunt explicabo.</p>
  <a class="more">LEARN MORE</a>
</div>

<section class="band abs" style="top:1692px;height:398px"></section>
<div class="feature abs" style="left:135px;top:1787px;width:600px">
  <h2>FLLIR/IR</h2>
  <p>Sed ut perspiciatis unde omnis iste natus error sit voluptatem accusantium doloremque laudantium, totam rem aperiam, eaque ipsa quae ab illo inventore veritatis et quasi architecto beatae vitae dicta sunt explicabo. Sed ut perspiciatis unde omnis iste natus error sit voluptatem accusantium doloremque laudantium.</p>
  <a class="more">LEARN MORE</a>
</div>
<div class="photo abs" style="left:765px;top:1739px;width:300px;height:300px;background:linear-gradient(160deg,#e7e5df,#9a9892 50%,#c5743a)" role="img" aria-label="Surveying total station on a tripod"></div>

<div class="photo abs" style="left:152px;top:2134px;width:286px;height:286px;background:linear-gradient(200deg,#f1c08a,#c48c6e 40%,#4e6b93)" role="img" aria-label="Industrial plant structures at sunset"></div>
<div class="feature abs" style="left:472px;top:2185px;width:653px">
  <h2>COMMERCIAL &amp; INDUSTRIAL INSPECTIONS</h2>
  <p>Tornwick, in affiliation with Vantor Aerial Works, provide UAV/Drone training from the fundamentals to specialized operations such as Aerial Videography, Tower Inspections, and more. Dale Ostrander, brings 20+ years of commercial.</p>
  <a class="more">LEARN MORE</a>
</div>

<section class="band abs" style="top:2470px;height:392px"></section>
<div class="feature abs" style="left:135px;top:2560px;width:600px">
  <h2>PUBLIC SERVICES: FIRE, LAW ENFORCEMENT<br>SEARCH AND RESCUE</h2>
  <p>Sed ut perspiciatis unde omnis iste natus error sit voluptatem accusantium doloremque laudantium, totam rem aperiam, eaque ipsa quae ab illo inventore veritatis et quasi architecto beatae vitae dicta sunt explicabo.</p>
  <a class="more">LEARN MORE</a>
</div>
<div class="photo abs" style="left:765px;top:2516px;width:300px;height:300px;background:linear-gradient(150deg,#d9dfe6,#b48a78 45%,#e08a4c 70%,#5b7fb4)" role="img" aria-label="Team of responders joining hands"></div>

<div class="about-head abs">
  <svg width="14" height="22" viewBox="0 0 14 22"><path d="M11 3L3 11l8 8" fill="none" stroke="#555" stroke-width="2.5"/></svg>
  <h2>ABOUT US</h2>
  <svg width="14" height="22" viewBox="0 0 14 22"><path d="M3 3l8 8-8 8" fill="none" stroke="#ccc" stroke-width="2.5"/></svg>
</div>
<article class="card abs" style="left:80px">
  <div class="avatar" role="img" aria-label="Portrait of Maren Holt"></div>
  <div><h3>MAREN HOLT – CEO</h3><p>Sed ut perspiciatis unde omnis iste natus error sit dlues voluptatem accusantium dolorem, Sed ut perspiciatis unde omnis iste natus.</p><a class="read">Read More</a></div>
</article>
<article class="card abs" style="left:617px">
  <div class="avatar" role="img" aria-label="Portrait of Dale Ostrander"></div>
  <div><h3>DALE OSTRANDER – CEO</h3><p>Sed ut perspiciatis unde omnis iste natus error sit dlues voluptatem accusantium dolorem, Sed ut perspiciatis unde omnis iste natus.</p><a class="read">Read More</a></div>
</article>

<section class="contact abs"></section>
<div class="contact-map abs" role="img" aria-label="Dotted world map background"></div>
<h2 class="contact-title abs">CONTACT US</h2>
<div class="contact-box abs">
  <p><span class="name">TORNWICK AVIATION</span> Neque porro quisquam est qui dolorem ipsum quia dolor sit amet, consectetur, adipisci velit.</p>
  <div class="contact-lines">
    <span><svg width="20" height="16" viewBox="0 0 20 16"><path d="M2 5c0-2 4-3 8-3s8 1 8 3v2h-4V5H6v2H2z" fill="#6289cc"/><rect x="4" y="8" width="12" height="7" rx="1" fill="#6289cc"/></svg>1800 555 0142</span>
    <span><svg width="20" height="14" viewBox="0 0 20 14"><rect x="1" y="1" width="18" height="12" fill="#6289cc"/><path d="M1 1l9 7 9-7" fill="none" stroke="#fff" stroke-width="1.5"/></svg>info@tornwickaviation.com</span>
  </div>
</div>

<footer class="site-footer abs"></footer>
<nav class="footer-nav abs">HOME<span>/</span>ABOUT US<span>/</span>SERVICES<span>/</span>BLOG<span>/</span>CONTACT US</nav>
<p class="copyright abs">(C) COPYRIGHT, 2016, ALL RIGHT RESERVED</p>
<div class="social abs" aria-label="Social media links"><span></span><span></span><span></span><span></span><span></span></div>

</body>
</html>
```